Civil Engineering Business Card Design

We need a business card design for an Civil Engineering Company located in Naples, Florida. The company name is Durvel Engineering.
What we do:
Site Evaluation
Review existing site conditions and zoning
Evaluation of potential development options
Evaluation of environmental permitting challenges
Prepare alternative master site development or redevelopment plan
Calculate cost and time lines for site development
Address political, environmental, social, and economic impacts of site development
Site Design
Prepare master site development plans
Zoning, rezoning, and zoning amendments for land use changes
Evaluate zoning and environmental permitting challenges
Value engineer alternative land development design and products
Residential Development
Plat development and design
Homeowner association document development
Single family development ranging from affordable housing to large estate projects
Multi family development ranging from duplexes to large scale condominiums
Amenity facilities such as golf courses, parks and clubhouse sites
Commercial Development
Office site and park designs development plans
Industrial site and park development plans
Shopping center site development design
Hospital site design development
Institutional Development
School design development and redevelopment plans
Park design development and enhancement plans
Downtown redevelopment plans for new and existing structures
Theater and park plan development
Parking garage design development
Governmental administration building design
Design Services
Site development
Environmental assessment
Roadway alignment and development
Surface water management
Drainage design
Water distribution system
Fire service analysis
Sewage collection systems
Sewage pump station and force main design
Cable utility conduit layout
Construction details
Construction documents
Technical specifications
Alternative methods and materials analysis
Services During Construction
Development of bid documents
Solicitation and processing of bids
Cost review and analysis
Construction cost estimating
Onsite construction observation
Coordination of field modifications to address unforeseen site conditions
Assess value engineering design and contract work
Review of pay requests and shop drawings
Review of warranties
Development assessment of onsite and offsite mitigation
Verification of construction completion, close out, and certification
Processing final pay requests and turn over
We want a clean design on a white background. We have a current logo but are not happy with it so changes would be greatly appreciated.
Industry/Entity Type
Construction
Contact Information for Business Card
Durvel Engineering
Creative Engineering Solutions Through Integrity and Experience
Marcus Pellow, President
4870 Brisket Ridge Road
Suite 517C
Naples, FL 34987
239-555-0164-Office, 239-555-0192-Mobile
Marcus@DurvelEng.example, www.DurvelEng.example

```html
<!DOCTYPE html>
<html lang="en">
<head>
<meta charset="utf-8">
<title>Durvel Engineering – Business Card</title>
<link rel="stylesheet" href="https://fonts.googleapis.com/css2?family=Source+Sans+3:ital,wght@0,400;0,600;0,700;1,400&display=swap">
<style>
  :root {
    --backdrop: #d6d7d9;
    --card: #ffffff;
    --slate: #3c4953;
    --brand-blue: #1f4ba3;
    --accent-blue: #2a56b8;
    --ink: #161616;
    --icon-disc: #dfe2e8;
  }
  * { margin: 0; padding: 0; box-sizing: border-box; }
  html, body {
    width: 1200px;
    height: 1200px;
    overflow: hidden;
  }
  body {
    background: var(--backdrop);
    font-family: "Source Sans 3", "Myriad Pro", Arial, sans-serif;
    position: relative;
  }
  .business-card {
    position: absolute;
    left: 148px;
    top: 344px;
    width: 902px;
    height: 513px;
    background: var(--card);
  }
  .brand-square {
    position: absolute;
    left: 228px;
    top: 36px;
    width: 56px;
    height: 56px;
    background: var(--brand-blue);
  }
  .company-name {
    position: absolute;
    left: 48px;
    top: 100px;
    font-size: 44px;
    font-weight: 700;
    letter-spacing: 0.3px;
    color: var(--slate);
    line-height: 1;
    white-space: nowrap;
  }
  .tagline {
    position: absolute;
    left: 48px;
    top: 200px;
    font-size: 25.5px;
    font-style: italic;
    color: var(--accent-blue);
    line-height: 31px;
  }
  .person {
    position: absolute;
    left: 48px;
    top: 358px;
  }
  .person-name {
    font-size: 29px;
    font-weight: 700;
    color: var(--ink);
    line-height: 36px;
  }
  .person-title {
    font-size: 25.5px;
    color: var(--accent-blue);
    line-height: 36px;
  }
  .contact-item {
    position: absolute;
    left: 476px;
    display: flex;
    align-items: flex-start;
    font-size: 25px;
    color: var(--ink);
    line-height: 31px;
    white-space: nowrap;
  }
  .contact-item svg {
    width: 24px;
    height: 24px;
    margin-top: 4px;
    margin-right: 16px;
    flex: none;
  }
  .contact-address { top: 202px; }
  .contact-office  { top: 328px; }
  .contact-mobile  { top: 365px; }
  .contact-email   { top: 399px; }
  .contact-web     { top: 435px; }
  .bottom-band {
    position: absolute;
    left: 0;
    bottom: 0;
    width: 100%;
    height: 34px;
    background: var(--brand-blue);
  }
</style>
</head>
<body>
  <div class="business-card">
    <div class="brand-square"></div>
    <div class="company-name">DURVEL ENGINEERING</div>

    <p class="tagline">Creative Engineering Solutions<br>Through Integrity and Experience</p>

    <div class="person">
      <p class="person-name">Marcus Pellow</p>
      <p class="person-title">President</p>
    </div>

    <div class="contact-item contact-address">
      <svg viewBox="0 0 24 24" aria-hidden="true">
        <circle cx="12" cy="12" r="12" fill="var(--icon-disc)"/>
        <path d="M12 5 L4.5 11.5 H7 V18 H10.5 V14 H13.5 V18 H17 V11.5 H19.5 Z" fill="var(--brand-blue)"/>
      </svg>
      <span>4870 Brisket Ridge Road,<br>Suite 517C, Naples, FL 34987</span>
    </div>

    <div class="contact-item contact-office">
      <svg viewBox="0 0 24 24" aria-hidden="true">
        <circle cx="12" cy="12" r="12" fill="var(--icon-disc)"/>
        <path d="M6 15.5 C6 12 9 8.5 14 7.5 L15.5 7.3 L16.3 9.6 L14.6 10.5 C11.8 11.2 10 13 9.4 15.3 L9.3 16.5 L6.5 16.8 Z" fill="var(--brand-blue)"/>
      </svg>
      <span>239-555-0164</span>
    </div>

    <div class="contact-item contact-mobile">
      <svg viewBox="0 0 24 24" aria-hidden="true">
        <circle cx="12" cy="12" r="12" fill="var(--icon-disc)"/>
        <rect x="8.5" y="5" width="7" height="14" rx="1.3" fill="var(--brand-blue)"/>
        <rect x="9.8" y="6.8" width="4.4" height="5" fill="var(--icon-disc)"/>
      </svg>
      <span>239-555-0192</span>
    </div>

    <div class="contact-item contact-email">
      <svg viewBox="0 0 24 24" aria-hidden="true">
        <circle cx="12" cy="12" r="12" fill="var(--icon-disc)"/>
        <rect x="5" y="7.5" width="14" height="9.5" fill="var(--brand-blue)"/>
        <path d="M5 7.5 L12 13 L19 7.5" fill="none" stroke="var(--icon-disc)" stroke-width="1.2"/>
      </svg>
      <span>Marcus@DurvelEng.example</span>
    </div>

    <div class="contact-item contact-web">
      <svg viewBox="0 0 24 24" aria-hidden="true">
        <circle cx="12" cy="12" r="12" fill="var(--icon-disc)"/>
        <g fill="none" stroke="var(--brand-blue)" stroke-width="1.5">
          <circle cx="12" cy="12" r="6.5"/>
          <ellipse cx="12" cy="12" rx="3" ry="6.5"/>
          <line x1="5.5" y1="12" x2="18.5" y2="12"/>
          <line x1="6.5" y1="9" x2="17.5" y2="9"/>
          <line x1="6.5" y1="15" x2="17.5" y2="15"/>
        </g>
      </svg>
      <span>www.DurvelEng.example</span>
    </div>

    <div class="bottom-band"></div>
  </div>
</body>
</html>
```